High profile consulting company needs a Business Card Design

I need a business card design for a coaching /consulting company. We specialize in changing behaviors. Our services include therapy, workshops, life coaching, etc.

Check out our website to get a feel for our personality. www.oakbridgeadvisory.com

The new logo will be attached to the website soon, I have attached the new logo for your use on the business card.
Updates

I forgot to provide you with the company email under the "must have" section for the business card.  The website is:

 www.oakbridgeadvisory.com

I understand there's some trouble with the logo I uploaded.  I will try that again.  Thank you for your efforts.

Dana

Thank you for some of your questions.  I prefer a one sided business card, and tend to like the white backgrounds.

I also made 2 small changes to the content.  

add MFT after the name:  Dana Holloway, MFT

and the tag line needed more clarity once I saw it.  Please change it to:  Improving performance by strengthening relationships and changing behaviors.

Thank you,
Dana

Industry/Entity Type

Business

Requirements
Must have
• logo
Phone number: 415-207-5146
email: Dana@oakbridgeadvisory.com
Dana Holloway, MFT
President
Nice to have
• Improving performance by strengthening relationships and changing behaviors.

```html
<!DOCTYPE html>
<html lang="en">
<head>
<meta charset="utf-8">
<title>Oakbridge Advisory – Business Cards</title>
<link href="https://fonts.googleapis.com/css2?family=Arimo:wght@400;700&display=swap" rel="stylesheet">
<style>
  :root {
    --bg: #2a2a2a;
    --card: #ffffff;
    --brand-green: #1f7a55;
    --deep-green: #0f5f40;
    --band-dark: #1a1a1a;
    --ink: #2b2b2b;
    --icon-grey: #333333;
    --on-green: #ffffff;
  }
  * { box-sizing: border-box; margin: 0; padding: 0; }
  html, body { width: 1200px; height: 944px; overflow: hidden; }
  body {
    background: var(--bg);
    font-family: "Arimo", Arial, sans-serif;
    position: relative;
  }
  .card {
    position: absolute;
    width: 560px;
    height: 320px;
    background: var(--card);
    border-radius: 22px;
    overflow: hidden;
    box-shadow: 0 10px 30px rgba(0,0,0,.45);
  }
  .card--brand { left: 60px; top: 130px; }
  .card--contact { left: 580px; top: 494px; }

  .wordmark {
    display: flex;
    align-items: center;
    gap: 14px;
    color: var(--brand-green);
    font-weight: 700;
    letter-spacing: .5px;
  }
  .wordmark__dot {
    border-radius: 50%;
    background: var(--brand-green);
    flex: none;
  }
  .card--brand .wordmark { position: absolute; left: 58px; top: 70px; font-size: 40px; }
  .card--brand .wordmark__dot { width: 56px; height: 56px; }

  .tagline {
    position: absolute;
    left: 0; right: 0; top: 200px;
    text-align: center;
    font-size: 15px;
    line-height: 1.3;
    color: var(--ink);
  }

  .card--contact .accent { position: absolute; inset: 0; }
  .card--contact .wordmark { position: absolute; left: 26px; top: 50px; font-size: 23px; gap: 10px; }
  .card--contact .wordmark__dot { width: 38px; height: 38px; }

  .contact-list {
    position: absolute;
    left: 28px; top: 200px;
    list-style: none;
    font-size: 14px;
    color: var(--ink);
  }
  .contact-list li { display: flex; align-items: center; gap: 10px; height: 21px; }
  .contact-list svg { width: 13px; height: 13px; flex: none; }

  .person {
    position: absolute;
    left: 362px; top: 158px;
    color: var(--on-green);
  }
  .person__name { font-size: 22px; font-weight: 400; }
  .person__title { font-size: 13px; margin-top: 5px; }
</style>
</head>
<body>

  <section class="card card--brand" aria-label="Business card, logo side">
    <div class="wordmark"><span class="wordmark__dot"></span>Oakbridge Advisory</div>
    <p class="tagline">Improving performance by<br>strengthening relationships and changing behaviors.</p>
  </section>

  <section class="card card--contact" aria-label="Business card, contact side">
    <svg class="accent" viewBox="0 0 560 320" preserveAspectRatio="none" aria-hidden="true">
      <defs>
        <linearGradient id="greenPanel" x1="0" y1="0" x2="1" y2="0">
          <stop offset="0" stop-color="var(--deep-green)"/>
          <stop offset="1" stop-color="var(--brand-green)"/>
        </linearGradient>
      </defs>
      <path d="M300 0 C345 90 345 230 322 320 L560 320 L560 0 Z" fill="var(--band-dark)"/>
      <path d="M318 0 C360 90 358 230 338 320 L560 320 L560 0 Z" fill="url(#greenPanel)"/>
    </svg>

    <div class="wordmark"><span class="wordmark__dot"></span>Oakbridge Advisory</div>

    <ul class="contact-list">
      <li>
        <svg viewBox="0 0 16 16"><path fill="var(--icon-grey)" d="M4 1h3l1 4-2 1.5a9 9 0 0 0 3.5 3.5L11 8l4 1v3c0 1.5-1 2-2 2C7 14 2 9 2 3c0-1 .5-2 2-2z"/></svg>
        415-207-5146
      </li>
      <li>
        <svg viewBox="0 0 16 16"><rect x="1" y="3" width="14" height="10" rx="2" fill="var(--icon-grey)"/><path d="M2 4l6 5 6-5" stroke="#fff" stroke-width="1.3" fill="none"/></svg>
        Dana@oakbridgeadvisory.com
      </li>
      <li>
        <svg viewBox="0 0 16 16"><circle cx="8" cy="8" r="7" fill="var(--icon-grey)"/></svg>
        www.oakbridgeadvisory.com
      </li>
    </ul>

    <div class="person">
      <p class="person__name">Dana Holloway</p>
      <p class="person__title">MFT, President</p>
    </div>
  </section>

</body>
</html>
```